TL - business card

Tallow Partners is an insurance brokerage firm, inovative, proactive, vigorous, which aims to become the leader of the insurance brokers in Anfrica. We should like to get some designs which should be avoided also in Gray / Metallic for the Administration and Orange / Blue for the Managers (ike in the picture sent). The Blue / Green logo is not the correct one, but the source of the file. Please adjust the color accordingly for the business cards. 1 / Orange / Blue 2 / Gray / Metallic We want something classic but which is transmitted strenght, inovation, modernity and most of all, rapidity. We want something start-up like, very punchy and catching eye remaining profesional at the same time. Name: Dorian Whitlock Function: Managing Director Address: N ° 17/18 Rua Veloso - R / C 2B Direita - Bairro Mutamba - Luanda Tel: (+244) 947 582 316 Email: dorian.whitlock@tallow-p.example Website: www.tallow-p. example We want classic in the front and creative, colorfull at the back. The cards will be printed in relief, with very high quality of paper.
Insurance Broker
Colors
Designer to choose colors to be used in the design.

```html
<!DOCTYPE html>
<html lang="en">
<head>
<meta charset="utf-8">
<title>Tallow Partners – Business Card</title>
<link rel="stylesheet" href="https://fonts.googleapis.com/css2?family=Lato:wght@400;700&family=Ubuntu:wght@700&display=swap">
<style>
  :root {
    --page: #2b2e33;
    --brand-blue: #0b7bc4;
    --brand-blue-deep: #0a6fb3;
    --brand-red: #e0302a;
    --brand-orange: #f39a57;
    --accent-orange: #ec7a3a;
    --ink: #3c3c3c;
    --ink-soft: #5a5a5a;
    --rule: #cfcfcf;
    --paper: #ffffff;
  }
  * { box-sizing: border-box; margin: 0; padding: 0; }
  html, body { width: 1200px; height: 1000px; overflow: hidden; }
  body {
    background: var(--page);
    font-family: "Lato", Arial, sans-serif;
    position: relative;
  }
  .card {
    position: absolute;
    left: 220px;
    width: 760px;
    height: 434px;
    overflow: hidden;
  }
  /* Back side */
  .card-back { top: 42px; background: var(--brand-blue); }
  .card-back .pattern-field {
    position: absolute; inset: 0;
    background: linear-gradient(135deg, var(--brand-blue) 0%, var(--brand-blue-deep) 100%);
  }
  .back-mark {
    position: absolute;
    left: 470px; top: 270px;
    display: flex; align-items: center; gap: 10px;
  }
  .back-mark .dot {
    width: 40px; height: 40px; border-radius: 50%;
    border: 4px solid var(--accent-orange);
  }
  .back-mark .mark-name {
    font-family: "Lato", Arial, sans-serif;
    font-weight: 700; font-size: 17px; color: var(--paper);
  }
  /* Front side */
  .card-front { top: 520px; background: var(--paper); }
  .holder { position: absolute; left: 58px; top: 58px; }
  .holder-name {
    font-family: "Ubuntu", Arial, sans-serif;
    font-weight: 700; font-size: 34px; color: var(--brand-blue);
    letter-spacing: 0.5px;
  }
  .holder-role { font-size: 18px; color: var(--ink-soft); margin-top: 2px; }
  .divider {
    position: absolute; left: 40px; top: 150px; width: 660px; height: 1px;
    background: linear-gradient(90deg, var(--brand-red) 0%, var(--accent-orange) 22%, var(--rule) 23%, var(--rule) 100%);
  }
  .contacts { position: absolute; left: 40px; top: 176px; list-style: none; }
  .contacts li {
    display: flex; align-items: center; gap: 12px;
    font-size: 18px; color: var(--ink); height: 34px;
  }
  .contacts svg { width: 18px; height: 18px; fill: var(--brand-blue); flex: none; }
  .firm-mark {
    position: absolute; right: 52px; top: 80px;
    display: flex; align-items: center; gap: 12px;
  }
  .firm-mark .dot {
    width: 54px; height: 54px; border-radius: 50%;
    border: 5px solid var(--accent-orange);
  }
  .firm-mark .firm-name {
    font-family: "Lato", Arial, sans-serif;
    font-weight: 700; font-size: 30px; color: var(--brand-blue);
    text-transform: uppercase; letter-spacing: 0.5px;
  }
  .address {
    position: absolute; right: 52px; top: 262px;
    text-align: right; font-size: 18px; line-height: 1.3; color: var(--ink);
  }
  .wave { position: absolute; left: 0; bottom: 0; width: 760px; height: 140px; }
</style>
</head>
<body>

<section class="card card-back" aria-label="Card back">
  <div class="pattern-field" role="img" aria-label="Repeating faint brand pattern on blue"></div>
  <div class="back-mark">
    <span class="dot"></span>
    <span class="mark-name">Tallow Partners</span>
  </div>
</section>

<section class="card card-front" aria-label="Card front">
  <div class="holder">
    <h1 class="holder-name">Dorian Whitlock</h1>
    <p class="holder-role">Managing Director</p>
  </div>

  <div class="firm-mark">
    <span class="dot"></span>
    <span class="firm-name">Tallow Partners</span>
  </div>

  <div class="divider"></div>

  <ul class="contacts">
    <li>
      <svg viewBox="0 0 24 24" aria-hidden="true"><path d="M6.6 10.8a15.2 15.2 0 0 0 6.6 6.6l2.2-2.2a1 1 0 0 1 1-.25 11.4 11.4 0 0 0 3.6.57 1 1 0 0 1 1 1V20a1 1 0 0 1-1 1A17 17 0 0 1 3 4a1 1 0 0 1 1-1h3.5a1 1 0 0 1 1 1c0 1.25.2 2.45.57 3.57a1 1 0 0 1-.25 1z"/></svg>
      (+244) 947 582 316
    </li>
    <li>
      <svg viewBox="0 0 24 24" aria-hidden="true"><path d="M2 5h20v14H2z M4 7v.4l8 5.2 8-5.2V7z" fill-rule="evenodd"/></svg>
      dorian.whitlock@tallow-p.example
    </li>
    <li>
      <svg viewBox="0 0 24 24" aria-hidden="true"><circle cx="12" cy="12" r="10"/></svg>
      www.tallow-p. example
    </li>
  </ul>

  <p class="address">N ° 17/18 Rua Veloso - R / C 2B<br>Direita - Bairro Mutamba - Luanda</p>

  <svg class="wave" viewBox="0 0 760 140" preserveAspectRatio="none" aria-hidden="true">
    <defs>
      <linearGradient id="waveFill" x1="0" x2="1" y1="0" y2="0">
        <stop offset="0" stop-color="#e0302a"/>
        <stop offset="1" stop-color="#f39a57"/>
      </linearGradient>
    </defs>
    <path d="M0 20 C180 100 420 60 760 128 L760 140 L0 140 Z" fill="url(#waveFill)"/>
    <path d="M0 14 C180 92 420 52 760 120" fill="none" stroke="#ffffff" stroke-width="5"/>
    <path d="M0 8 C180 86 420 46 760 116" fill="none" stroke="#0b7bc4" stroke-width="4"/>
    <path d="M0 2 C180 78 420 40 700 92" fill="none" stroke="#e0302a" stroke-width="2"/>
  </svg>
</section>

</body>
</html>
```